Business Report Cover

We need a revamped quarterly report cover to send to our clients. We asset manage commercial and residential properties throughout the the United States. We use a .pdf version of a cover that we've used for years but would like a fresh updated look for 2018. The cover should include our company logo (KOV Enterprises) and a photo of the property as well as the Quarter/Year of the report.

```html
<!DOCTYPE html>
<html lang="en">
<head>
<meta charset="utf-8">
<title>KOV Enterprises – Quarterly Operating Report</title>
<link href="https://fonts.googleapis.com/css2?family=Questrial&family=Open+Sans:ital,wght@0,700;1,700&display=swap" rel="stylesheet">
<style>
  :root{
    --stage:#e9ecec;
    --paper:#ffffff;
    --brown:#6a4541;
    --cream:#f4ece2;
    --gold-text:#efd98c;
    --gold-a:#f8d84e;
    --gold-b:#f2a700;
    --ink:#151515;
    --accent:#1e8a5a;
    --sky:#5ab8e6;
  }
  *{margin:0;padding:0;box-sizing:border-box}
  html,body{width:1200px;height:1200px;overflow:hidden;background:var(--stage)}
  .cover{
    position:absolute;left:160px;top:30px;width:880px;height:1140px;
    background:var(--paper);overflow:hidden;
    box-shadow:0 10px 30px rgba(0,0,0,.18);
  }
  .property-photo{
    position:absolute;left:48px;top:48px;right:48px;bottom:48px;
    background:linear-gradient(180deg,var(--sky) 0%,#cfe6f3 32%,#6e8b5a 46%,#8c4a36 56%,#5d5a58 64%,#6c6764 70%);
  }
  .brand-tab{
    position:absolute;right:48px;top:48px;width:300px;height:150px;
    background:var(--paper);border-bottom-left-radius:44px;
    display:flex;align-items:center;justify-content:center;gap:12px;
  }
  .brand-mark{width:14px;height:14px;border-radius:50%;background:var(--accent)}
  .brand-name{font-family:"Open Sans",sans-serif;font-weight:700;font-size:30px;color:var(--ink);letter-spacing:.5px}
  .title-panel{
    position:absolute;left:48px;right:48px;top:560px;bottom:48px;
    background:linear-gradient(180deg,rgba(106,69,65,0) 0%,rgba(106,69,65,.85) 20%,var(--brown) 34%);
  }
  .title-frame{
    position:absolute;left:30px;top:190px;width:580px;height:210px;
    border:3px solid var(--cream);border-radius:34px;
  }
  .title-kicker{
    position:absolute;left:90px;top:-28px;padding:0 16px;background:var(--brown);
    font-family:"Questrial",sans-serif;font-weight:400;font-size:42px;line-height:1.2;color:var(--cream);white-space:nowrap;
  }
  .title-main{
    position:absolute;left:28px;top:44px;
    font-family:"Questrial",sans-serif;font-weight:400;font-size:124px;line-height:1;color:var(--gold-text);white-space:nowrap;
  }
  .quarter-flag{position:absolute;right:0;top:150px;width:170px;height:300px}
  .quarter-label{
    position:absolute;right:14px;top:326px;text-align:right;color:var(--brown);
    font-family:"Open Sans",sans-serif;font-weight:700;line-height:1;
  }
  .quarter-label .q-num{font-size:48px;display:block}
  .quarter-label .q-word{font-size:22px;display:block;margin-top:4px}
  .quarter-label .q-year{font-family:"Questrial",sans-serif;font-size:24px;font-weight:400;display:block;margin-top:2px}
  .property-address{
    position:absolute;left:40px;top:420px;
    font-family:"Open Sans",sans-serif;font-style:italic;font-weight:700;font-size:20px;line-height:1.3;color:var(--cream);
  }
</style>
</head>
<body>
  <main class="cover">
    <div class="property-photo" role="img" aria-label="Photo of the property: a brick convenience store with a fuel canopy and pumps under a blue sky with evergreen trees"></div>

    <div class="brand-tab">
      <span class="brand-mark"></span>
      <span class="brand-name">KOV Enterprises</span>
    </div>

    <section class="title-panel">
      <div class="title-frame">
        <h2 class="title-kicker">Quarterly Operating</h2>
        <h1 class="title-main">REPORT</h1>
      </div>

      <svg class="quarter-flag" viewBox="0 0 170 300" aria-hidden="true">
        <defs>
          <linearGradient id="goldFill" x1="0" y1="0" x2="1" y2="1">
            <stop offset="0" stop-color="#f8d84e"/>
            <stop offset="1" stop-color="#f2a700"/>
          </linearGradient>
        </defs>
        <polygon points="170,0 170,300 20,300" fill="url(#goldFill)"/>
      </svg>
      <p class="quarter-label">
        <span class="q-num">1st</span>
        <span class="q-word">Quarter</span>
        <span class="q-year">2018</span>
      </p>

      <address class="property-address">
        Vancouver Quick-Stop<br>
        4120 NE Harbor View Dr.<br>
        Vancouver, WA 98660
      </address>
    </section>
  </main>
</body>
</html>
```